Stationery Design Project

I need a design that is simple, clean and modern, in square style, bold font.
The majority of the design needs to be White and Black with a splash of Red colour.
I would like a design for business cards and letter heads with the following information.
Name, Title, Phone, Fax, Email, Website and company ABN number

Target Market(s)

25 to 65 years old real estate clients

Industry/Entity Type

Business

Requirements
Must have
• All designs must incorporate Company Logo, Name, Title, Phone, Fax, Email, Website and company ABN number

```html
<!DOCTYPE html>
<html lang="en">
<head>
<meta charset="utf-8">
<title>Halden Real Estate – Business Card</title>
<link rel="stylesheet" href="https://fonts.googleapis.com/css2?family=Source+Sans+3:wght@400;600;700&display=swap">
<style>
  :root {
    --backdrop: #7a4526;
    --card-white: #ffffff;
    --brand-red: #d62a27;
    --ink: #231f20;
    --ink-soft: #3a3536;
    --rule: #555555;
  }
  * { margin: 0; padding: 0; box-sizing: border-box; }
  html, body { width: 1200px; height: 402px; overflow: hidden; }
  body {
    background: var(--backdrop);
    font-family: "Source Sans 3", "Myriad Pro", Arial, sans-serif;
    position: relative;
  }
  .card {
    position: absolute;
    top: 36px;
    width: 513px;
    height: 292px;
    box-shadow: 0 2px 6px rgba(0,0,0,.35);
  }
  .card--front { left: 66px; background: var(--card-white); }
  .card--back { left: 632px; background: var(--brand-red); }

  .brand-frame {
    position: absolute;
    border-style: solid;
    display: flex;
    flex-direction: column;
    align-items: center;
    justify-content: center;
  }
  .card--front .brand-frame {
    left: 21px; top: 24px; width: 204px; height: 114px;
    border-width: 3px; border-color: var(--ink); border-radius: 14px;
    color: var(--ink);
  }
  .card--back .brand-frame {
    left: 103px; top: 42px; width: 305px; height: 169px;
    border-width: 4px; border-color: var(--card-white); border-radius: 22px;
    color: var(--card-white);
  }
  .brand-name, .brand-tag { font-weight: 600; line-height: 1; }
  .card--front .brand-name { font-size: 38px; letter-spacing: 1px; }
  .card--front .brand-tag { font-size: 10px; letter-spacing: 6px; margin-top: 10px; margin-left: 6px; }
  .card--back .brand-name { font-size: 58px; letter-spacing: 2px; }
  .card--back .brand-tag { font-size: 15px; letter-spacing: 10px; margin-top: 16px; margin-left: 10px; }

  .name-band {
    position: absolute; top: 157px; height: 42px;
    background: var(--brand-red);
  }
  .name-band--main { left: 0; width: 337px; }
  .name-band--end { left: 399px; width: 114px; }
  .accent-square {
    position: absolute; top: 157px; left: 342px; width: 52px; height: 42px;
    background: var(--ink);
  }
  .person {
    position: absolute; left: 30px; top: 168px;
    color: var(--card-white); font-size: 16px; line-height: 20px;
  }
  .person strong { font-weight: 700; font-size: 17px; }
  .person span { font-size: 13px; }

  .contact-list {
    position: absolute; left: 32px; top: 222px;
    list-style: none; color: var(--ink-soft); font-size: 13.5px;
  }
  .contact-list li { display: flex; align-items: center; height: 17px; }
  .contact-list svg { width: 10px; height: 10px; margin-right: 6px; fill: var(--brand-red); }
  .contact-divider {
    position: absolute; left: 181px; top: 242px; width: 1px; height: 42px;
    background: var(--rule);
  }
  .address {
    position: absolute; left: 203px; top: 252px;
    color: var(--ink-soft); font-size: 13.5px; line-height: 17px;
  }
  .abn {
    position: absolute; left: 0; right: 0; top: 234px;
    text-align: center; color: var(--card-white); font-size: 16px;
  }
</style>
</head>
<body>
  <section class="card card--front">
    <div class="brand-frame">
      <div class="brand-name">HALDEN</div>
      <div class="brand-tag">REAL ESTATE</div>
    </div>
    <div class="name-band name-band--main"></div>
    <div class="accent-square"></div>
    <div class="name-band name-band--end"></div>
    <p class="person"><strong>Your name,</strong> <span>Title</span></p>
    <ul class="contact-list">
      <li><svg viewBox="0 0 10 10"><circle cx="5" cy="5" r="5"/><path d="M3 2.5l1 1.3-.6.8a4 4 0 0 0 2 2l.8-.6 1.3 1-.6 1C4.6 8 2 5.4 2 3.1z" fill="#fff"/></svg>123-456-7890</li>
      <li><svg viewBox="0 0 10 10"><rect x="2.5" y="0.5" width="5" height="3"/><rect x="0" y="4" width="10" height="4" rx="1"/><rect x="2.5" y="7" width="5" height="3"/></svg>123-456-7890</li>
      <li><svg viewBox="0 0 10 10"><rect x="0" y="2" width="10" height="6.5"/><path d="M0.5 2.5L5 6l4.5-3.5" stroke="#fff" stroke-width="1" fill="none"/></svg>info@haldenmail.com</li>
      <li><svg viewBox="0 0 10 10"><circle cx="5" cy="5" r="5"/><path d="M0 5h10M5 0v10" stroke="#fff" stroke-width=".8"/></svg>www.website.com</li>
    </ul>
    <div class="contact-divider"></div>
    <p class="address">Street Name, City Name<br>State, City Zip Code</p>
  </section>

  <section class="card card--back">
    <div class="brand-frame">
      <div class="brand-name">HALDEN</div>
      <div class="brand-tag">REAL ESTATE</div>
    </div>
    <p class="abn">ABN;123456789</p>
  </section>
</body>
</html>
```